eCommerce website for a DIY shop & communal center

We need a website for a business called The Maple Bench. The Maple Bench is both a shop and communal establishment where people with shared interests, especially in DIY (Do It Yourself) and crafting, can gather to shop for & work on projects while sharing ideas, equipment, supplies and knowledge. The shop is both brick & motor and online. The physical communal space provides workstations, equipment, tools and supplies and expertise for DIY lovers to create their projects.

Target Market(s)

Middle & upper class DIY enthusiasts, creative hobbyists, budding artists & small business owners

Industry/Entity Type

DIY, Arts & Crafts

Coding

Coded - Design and coding required

Number of Pages Required

5+ page

Requirements
Must have
• Menus to include 1. home page (with about us, operating hours, contacts, location, meet the team); 2. Bench activities (how to DIY at the Bench, booking, equipment & tools, house rules); 3. Bench events (events in the Bench, offsite events); 4. Resources (FAQs, tutorials, blogs, eBooks) and 5. Online shop
Nice to have
• Branding guidelines eg logo colours (see attachment) to influence design. Tillpost shop. Booking feature for activities & events at the Bench.

```html
<!DOCTYPE html>
<html lang="en">
<head>
<meta charset="utf-8">
<title>The Maple Bench — Bench Activities</title>
<link rel="stylesheet" href="https://fonts.googleapis.com/css2?family=Roboto:wght@400;500;700&family=Alex+Brush&display=swap">
<style>
:root{
  --orange:#f37f36;
  --blue:#2f86c8;
  --ink:#1d1d1d;
  --navy:#17233a;
  --grey:#555;
  --line:#e4e4e4;
  --footer:#121212;
  --white:#fff;
}
*{box-sizing:border-box;margin:0;padding:0}
html,body{width:1200px;height:3133px;overflow:hidden}
body{position:relative;background:var(--white);font-family:'Roboto',sans-serif;color:var(--ink)}
.abs{position:absolute}
.script{font-family:'Alex Brush',cursive;font-weight:400}
.o{color:var(--orange)}.b{color:var(--blue)}

/* header */
.topbar-phone{left:101px;top:6px;display:flex;align-items:center;gap:12px;font-size:15px}
.ring{width:36px;height:36px;border:1.5px solid #9a9a9a;border-radius:50%;display:flex;align-items:center;justify-content:center}
.socials-top{right:102px;top:5px;display:flex;gap:7px}
.header-rule{left:0;top:49px;width:1200px;height:1px;background:var(--line)}
.nav{top:63px;font-size:15px;font-weight:500;letter-spacing:.2px;color:var(--ink)}
.logo-disc{left:530px;top:0;width:170px;height:134px;background:var(--white);border-radius:0 0 85px 85px;z-index:3;display:flex;flex-direction:column;align-items:center;justify-content:center;box-shadow:0 2px 3px rgba(0,0,0,.15)}
.logo-name{font-size:21px;font-weight:700;color:var(--orange);text-align:center;line-height:1.15}

/* hero */
.hero{left:0;top:101px;width:1200px;height:370px;background:linear-gradient(100deg,#3b2a20 0%,#5a4232 35%,#8a6248 60%,#b8876a 80%,#d7b28f 100%)}
.hero h1{position:absolute;left:101px;top:138px;font-size:58px;font-weight:700;color:var(--white);letter-spacing:.5px}

/* sections */
.sec-title{width:1200px;left:0;text-align:center;font-size:50px;line-height:1}
.intro{width:1200px;left:0;text-align:center;font-size:15px;line-height:25px;color:#444}
.card-img{height:231px;width:322px}
.card-title{font-size:22px;font-weight:500;color:var(--navy)}
.card-text{width:322px;font-size:13.3px;line-height:25.5px;color:#555}

.band{left:0;top:1121px;width:1200px;height:365px;background:var(--orange)}
.band .sec-title{color:var(--white);top:66px}
.band p{position:absolute;left:0;top:138px;width:1200px;text-align:center;color:var(--white);font-size:15px;line-height:27px}
.btn-book{position:absolute;left:509px;top:251px;width:182px;height:47px;border-radius:24px;background:var(--white);color:var(--orange);font-weight:500;font-size:14px;display:flex;align-items:center;justify-content:center}

.wash-blue{left:0;top:1900px;width:1200px;height:360px;background:radial-gradient(ellipse at 50% 50%,rgba(120,185,225,.55),rgba(170,210,235,.35) 55%,rgba(255,255,255,0) 75%)}
.tool-img{top:1733px;width:319px;height:368px;box-shadow:0 0 4px rgba(0,0,0,.15)}
.tool-cap{top:2116px;width:340px;text-align:center;font-size:23px;font-weight:500;color:#222}
.arrow{top:1912px}

.wash-pink{left:55px;top:2235px;width:560px;height:440px;background:radial-gradient(ellipse at 45% 55%,rgba(245,150,120,.55),rgba(250,200,160,.35) 50%,rgba(255,255,255,0) 72%)}
.rules{left:132px;top:2345px;list-style:none}
.rules li{display:flex;align-items:center;gap:8px;font-size:22px;height:39px;color:#222}
.dot{width:19px;height:19px;border:2px solid #111;border-radius:50%;display:flex;align-items:center;justify-content:center}
.dot::after{content:"";width:9px;height:9px;border-radius:50%;background:#111}

/* footer */
.footer{left:0;top:2760px;width:1200px;height:373px;background:var(--footer);color:var(--white)}
.fcol{position:absolute;top:79px}
.fcol h4{font-size:16px;font-weight:700;margin-bottom:12px;letter-spacing:.2px}
.fcol li{list-style:none;font-size:14px;line-height:28px}
.email{position:absolute;left:843px;top:110px;width:256px;height:41px;border-radius:21px;background:var(--white);color:#333;font-size:13px;padding-left:15px;display:flex;align-items:center}
.subscribe{position:absolute;left:843px;top:160px;width:256px;height:41px;border-radius:21px;background:var(--orange);font-size:14px;font-weight:700;display:flex;align-items:center;justify-content:center}
.fsocial{position:absolute;top:222px;width:36px;height:36px;border-radius:50%;background:var(--white)}
.frule{position:absolute;left:101px;top:292px;width:998px;height:1px;background:#2e2e2e}
.copy{position:absolute;left:0;top:310px;width:1200px;text-align:center;font-size:13px}
</style>
</head>
<body>

<header>
  <div class="abs topbar-phone">
    <span class="ring"><svg width="16" height="16" viewBox="0 0 24 24"><path fill="#777" d="M6.6 10.8a15.1 15.1 0 0 0 6.6 6.6l2.2-2.2c.3-.3.7-.4 1-.2 1.1.4 2.3.6 3.6.6.6 0 1 .4 1 1V20c0 .6-.4 1-1 1A17 17 0 0 1 3 4c0-.6.4-1 1-1h3.5c.6 0 1 .4 1 1 0 1.3.2 2.5.6 3.6.1.3 0 .7-.2 1z"/></svg></span>
    <span>888 - 888 - 8888</span>
  </div>
  <div class="abs socials-top" aria-label="Social links">
    <span class="ring"></span><span class="ring"></span><span class="ring"></span><span class="ring"></span>
  </div>
  <div class="abs header-rule"></div>
  <nav>
    <span class="abs nav" style="left:99px">HOME</span>
    <span class="abs nav" style="left:195px">BENCH ACTIVITIES</span>
    <span class="abs nav" style="left:380px">BENCH EVENTS</span>
    <span class="abs nav" style="left:704px">RESOURCES</span>
    <span class="abs nav" style="left:849px">ONLINE SHOP</span>
    <span class="abs nav" style="left:1007px">CONTACT US</span>
  </nav>
  <div class="abs logo-disc"><div class="logo-name">The Maple<br>Bench</div></div>
</header>

<section class="abs hero" role="img" aria-label="Woman sketching at a workshop bench with ear defenders and wood blocks">
  <h1>BENCH ACTIVITIES</h1>
</section>

<section>
  <h2 class="abs sec-title script" style="top:530px"><span class="o">Everyday</span> <span class="b">Activities</span></h2>
  <p class="abs intro" style="top:594px">Lorem ipsum dolor sit amet, consectetur adipiscing elit, sed do eiusmod tempor incididunt ut labore<br>et dolore magna aliqua. Quis ipsum suspendisse ultrices gravida.</p>

  <div class="abs card-img" style="left:101px;top:677px;background:linear-gradient(160deg,#d9d3c7,#b9b2a6 55%,#3a3530)" role="img" aria-label="Member pouring paint onto a canvas tray"></div>
  <div class="abs card-img" style="left:440px;top:677px;background:linear-gradient(160deg,#8e8a80,#6a5a48 55%,#c9b9a0)" role="img" aria-label="Member drilling a wood piece in the workshop"></div>
  <div class="abs card-img" style="left:778px;top:677px;background:linear-gradient(160deg,#8e8a80,#6a5a48 55%,#c9b9a0)" role="img" aria-label="Member drilling a wood piece in the workshop"></div>

  <h3 class="abs card-title" style="left:101px;top:922px">ACTIVITIES NAME</h3>
  <h3 class="abs card-title" style="left:440px;top:922px">ACTIVITIES NAME</h3>
  <h3 class="abs card-title" style="left:778px;top:922px">ACTIVITIES NAME</h3>
  <p class="abs card-text" style="left:101px;top:955px">Lorem ipsum dolor sit amet, consectetur adipiscing elit, sed do eiusmod tempor incididunt ut labore et dolore magna aliqua ultrices gravida.</p>
  <p class="abs card-text" style="left:440px;top:955px">Lorem ipsum dolor sit amet, consectetur adipiscing elit, sed do eiusmod tempor incididunt ut labore et dolore magna aliqua ultrices gravida.</p>
  <p class="abs card-text" style="left:778px;top:955px">Lorem ipsum dolor sit amet, consectetur adipiscing elit, sed do eiusmod tempor incididunt ut labore et dolore magna aliqua ultrices gravida.</p>
</section>

<section class="abs band">
  <h2 class="abs sec-title script">Book Your Orders</h2>
  <p>Sed ut perspiciatis unde omnis iste natus errluptatem accusantium doloremque laudantium, totam rem aperiam, eaque ipsa quae ab<br>illo inventore veritatis et quasi architecto beatae e dicta sunt explicabo. Nemo enim ipsam voluptatem quia voluptas sit aspernatur aut<br>odit aut fugit, sed quia consequuntur magni &nbsp;eos qui ratione voluptatem sequi nesciunt. Neque porro quisquam</p>
  <span class="btn-book">BOOK NOW</span>
</section>

<section>
  <div class="abs wash-blue" aria-hidden="true"></div>
  <h2 class="abs sec-title script" style="top:1592px"><span class="o">Equipment &amp;</span> <span class="b">Tools</span></h2>
  <p class="abs intro" style="top:1651px">Lorem ipsum dolor sit amet, consectetur adipiscing elit, sed do eiusmod tempor incididunt ut labore<br>et dolore magna aliqua. Quis ipsum suspendisse ultrices gravida.</p>

  <div class="abs tool-img" style="left:102px;background:linear-gradient(150deg,#e9e4dc,#b89a7a 60%,#8a6a4c)" role="img" aria-label="Cordless drill and screws on a wooden board"></div>
  <div class="abs tool-img" style="left:441px;background:linear-gradient(150deg,#cdbfa8,#efe4cf 50%,#d8c6a6)" role="img" aria-label="Pine boards with a square and router"></div>
  <div class="abs tool-img" style="left:779px;background:linear-gradient(160deg,#5a4636,#7b6552 45%,#a89a8a)" role="img" aria-label="Circular saw on a workbench"></div>

  <p class="abs tool-cap" style="left:92px">Sed ut perspiciatis und</p>
  <p class="abs tool-cap" style="left:430px">Sed ut perspiciatis und</p>
  <p class="abs tool-cap" style="left:769px">Sed ut perspiciatis und</p>

  <svg class="abs arrow" style="left:64px" width="18" height="36" viewBox="0 0 18 36"><path d="M16 2 2 18l14 16" fill="none" stroke="#333" stroke-width="1.6"/></svg>
  <svg class="abs arrow" style="left:1117px" width="18" height="36" viewBox="0 0 18 36"><path d="M2 2l14 16L2 34" fill="none" stroke="#333" stroke-width="1.6"/></svg>
</section>

<section>
  <div class="abs wash-pink" aria-hidden="true"></div>
  <h2 class="abs script" style="left:126px;top:2262px;font-size:50px"><span class="o">House</span> <span class="b">Rules</span></h2>
  <ul class="abs rules">
    <li><span class="dot"></span>Sed ut perspiciatis unde omnis iste natus</li>
    <li><span class="dot"></span>Sed ut perspiciatis unde omnis iste natus</li>
    <li><span class="dot"></span>Sed ut perspiciatis unde omnis iste natus</li>
    <li><span class="dot"></span>Sed ut perspiciatis unde omnis iste natus</li>
    <li><span class="dot"></span>Sed ut perspiciatis unde omnis iste natus</li>
    <li><span class="dot"></span>Sed ut perspiciatis unde omnis iste natus</li>
  </ul>
  <div class="abs" style="left:601px;top:2235px;width:498px;height:413px;background:linear-gradient(170deg,#4d6a3a,#7b8a5a 40%,#8a7058 75%,#5a4a3c)" role="img" aria-label="Group working on wood projects at an outdoor table"></div>
</section>

<footer class="abs footer">
  <div class="fcol" style="left:101px"><h4>ABOUT</h4><ul><li>Our Story</li><li>Press</li><li>Locations</li><li>Blog</li><li>Contact Us</li></ul></div>
  <div class="fcol" style="left:236px"><h4>OUR OFFERING</h4><ul><li>Projects</li><li>Paint Room</li><li>Parties</li><li>Classes</li></ul></div>
  <div class="fcol" style="left:421px"><h4>OTHER</h4><ul><li>Franchise</li><li>Gift Cards</li><li>FAQ</li><li>Refund Policy</li></ul></div>
  <div class="fcol" style="left:571px"><h4>CONTACT US</h4><ul><li>1234 Somestreet Anywhere USA</li><li>21212</li><li>888 - 888 - 8888</li><li>info@maplebench.com</li></ul></div>
  <div class="fcol" style="left:843px"><h4>GET UPDATES &amp; PROMOS</h4></div>
  <div class="email">Email Address</div>
  <div class="subscribe">SUBSCRIBE</div>
  <span class="fsocial" style="left:851px"></span>
  <span class="fsocial" style="left:893px"></span>
  <span class="fsocial" style="left:934px"></span>
  <span class="fsocial" style="left:977px"></span>
  <div class="frule"></div>
  <p class="copy">Copyright © 2021 The Maple Bench. All rights reserved.</p>
</footer>

</body>
</html>
```